Website Design for a holiday home letting busines

We require a redesign of our present website www.pinebrookstays.com. We want the website to stand out and look professional and clean to make holiday hunters want to book a caravan or lodge holiday with us. Our logo is red however we DO NOT want the website to be red. We want a natural colour scheme.

The final design should communicate that we are a professional company to book with.

On the home page we require;
Overview of company
Photo
Search box for holiday (check in)
Late Deals
Reviews
News

We would like the following pages designed; home page, available dates page, caravans page, content page.

The website should be responsive for smart phones. One website I do like is http://www.verdoliso.be/nl/

Target Market(s)

Families

Industry/Entity Type

Travel

Number of Pages Required

5+ page

Font styles to use
Serif

Requirements
Must have
• The project must be responsive for mobile phones and tablets.
• Ability to search for holiday home holidays
• We want a natural colour scheme.
Nice to have
• A style we like is http://www.verdoliso.be/nl/
Should not have
• Do not use red as a colour for the website. Our logo is red so this is the only time we want this used.

```html
<!DOCTYPE html>
<html lang="en">
<head>
<meta charset="utf-8">
<title>Pinebrook Stays – Private Holiday Rentals</title>
<link href="https://fonts.googleapis.com/css2?family=Open+Sans:wght@400;600;700;800&display=swap" rel="stylesheet">
<style>
:root{
  --accent:#1ba3dd;
  --accent-dark:#1486b8;
  --ink:#333;
  --muted:#777;
  --line:#e3e3e3;
  --nav:#3b3d40;
  --footer:#26282b;
  --footer-2:#1d1f21;
  --soft:#f4f4f4;
  --logo:#d23a2c;
  --white:#fff;
}
*{box-sizing:border-box;margin:0;padding:0}
html,body{width:1200px;height:3040px;overflow:hidden}
body{font-family:"Open Sans",Arial,sans-serif;color:var(--ink);background:var(--white);font-size:13px;line-height:1.6}
.wrap{width:1080px;margin:0 auto;position:relative}
.btn{display:inline-block;background:var(--accent);color:var(--white);font-weight:700;font-size:12px;letter-spacing:1px;text-transform:uppercase;padding:9px 22px}
.section-title{text-align:center;font-weight:700;font-size:32px;letter-spacing:1px;text-transform:uppercase;color:#2d2d2d}
.section-title::after{content:"";display:block;width:60px;height:3px;background:var(--accent);margin:12px auto 0}

/* header */
.site-header{height:128px}
.site-header .wrap{height:128px;display:flex;justify-content:space-between;align-items:center}
.brand{display:flex;align-items:center;gap:12px}
.brand-mark{width:40px;height:40px;border-radius:50%;background:var(--logo)}
.brand-name{font-size:28px;font-weight:700;color:var(--logo);line-height:1}
.brand-sub{font-size:11px;color:var(--muted);margin-top:4px}
.header-info{text-align:right}
.social{display:flex;gap:6px;justify-content:flex-end;margin-bottom:12px}
.social span{width:26px;height:26px;border:1px solid #ccc;border-radius:3px;display:block}
.contact-line{display:flex;align-items:center;justify-content:flex-end;gap:8px;font-size:18px;font-weight:700;color:var(--accent)}
.contact-mail{font-size:12px;color:var(--muted);display:flex;gap:6px;justify-content:flex-end;align-items:center}

/* nav */
.main-nav{height:52px;background:var(--nav)}
.main-nav ul{list-style:none;display:flex;height:52px;width:1080px;margin:0 auto}
.main-nav li{color:#e6e6e6;font-size:13px;font-weight:600;padding:0 22px;display:flex;align-items:center}
.main-nav li.active{background:var(--accent);color:var(--white)}

/* hero */
.hero{height:620px;position:relative;overflow:hidden}
.hero-bg{position:absolute;inset:0;background:linear-gradient(180deg,#8fc0e6 0%,#c7e2f2 45%,#9cc25a 62%,#6e9a33 100%)}
.hero-copy{position:absolute;left:60px;top:110px;width:420px;color:var(--white)}
.hero-copy h1{font-size:34px;font-weight:800;letter-spacing:.5px;text-shadow:0 1px 3px rgba(0,0,0,.25)}
.hero-copy p{font-size:17px;font-weight:600;margin-top:10px;text-shadow:0 1px 2px rgba(0,0,0,.25)}
.search-box{position:absolute;left:60px;top:300px;width:400px;background:rgba(255,255,255,.88);padding:18px 20px}
.search-fields{display:flex;gap:14px}
.field label{display:block;font-size:12px;font-weight:700;color:#444;margin-bottom:4px}
.field .input{width:170px;height:32px;border:1px solid #ccc;background:var(--white);font-size:11px;color:#999;padding:7px 10px}
.search-box .btn{float:right;margin-top:14px}
.hero-circle{position:absolute;left:590px;top:40px;width:430px;height:430px;border-radius:50%;border:10px solid rgba(255,255,255,.9);background:radial-gradient(circle at 50% 40%,#e9ddc6,#b89a74 70%,#8a7457)}
.hero-arrows{position:absolute;left:60px;bottom:40px;display:flex;gap:6px}
.hero-arrows span{width:30px;height:30px;background:rgba(255,255,255,.6);display:flex;align-items:center;justify-content:center}

/* overview */
.overview{height:260px;padding-top:56px;text-align:center}
.overview p{width:900px;margin:26px auto 20px;color:var(--muted);font-size:13px}

/* late deals */
.late-deals{height:420px;position:relative}
.late-bg{position:absolute;inset:0;background:linear-gradient(180deg,#2b2420 0%,#4b3a2e 55%,#2a211c 100%)}
.late-deals .section-title{position:relative;color:var(--white);padding-top:52px}
.deal-grid{position:relative;display:flex;gap:40px;justify-content:center;margin-top:34px}
.deal-card{width:300px;background:var(--white);position:relative}
.deal-photo{height:140px;background:linear-gradient(135deg,#d9cdb8,#9d8a6f)}
.book-badge{position:absolute;right:-14px;top:-14px;width:62px;height:62px;border-radius:50%;background:var(--accent);color:var(--white);font-size:10px;font-weight:700;text-align:center;line-height:1.25;display:flex;align-items:center;justify-content:center;border:3px solid var(--white)}
.deal-body{padding:10px 14px}
.deal-body h3{font-size:13px;font-weight:700}
.deal-body p{font-size:11px;font-weight:700;color:#555}
.dots{position:relative;display:flex;gap:6px;justify-content:center;margin-top:20px}
.dots span{width:10px;height:10px;border-radius:50%;background:#bbb}
.dots span.on{background:var(--white)}

/* caravans */
.caravans{height:640px;padding-top:58px}
.caravan-grid{display:grid;grid-template-columns:1fr 1fr;gap:30px 40px;width:1000px;margin:40px auto 0}
.caravan-card{border:1px solid var(--line);padding:16px;display:flex;gap:18px;height:200px}
.caravan-photo{width:200px;height:166px;background:linear-gradient(135deg,#e2d7c5,#a99275)}
.caravan-info h3{font-size:15px;font-weight:700;margin-bottom:8px}
.specs{display:grid;grid-template-columns:90px 90px;font-size:12px;color:var(--muted);row-gap:2px}
.caravan-info .btn{margin-top:14px;font-size:11px;padding:7px 18px}

/* feeds */
.feeds{height:640px;background:var(--soft);padding-top:60px}
.feeds .wrap{display:flex;gap:50px}
.feed-col{flex:1}
.feed-col h2{font-size:21px;font-weight:700;text-transform:uppercase;margin-bottom:24px}
.review{margin-bottom:26px}
.review h4{color:var(--accent);font-size:12px;font-weight:700;text-transform:uppercase}
.review .meta{font-size:13px;font-weight:600;color:#555}
.stars{color:#f0a81e;letter-spacing:1px}
.review p,.post p{font-size:12px;color:var(--muted)}
.more{color:var(--accent);font-weight:600}
.post{display:flex;gap:14px;margin-bottom:24px}
.post-icon{width:34px;height:34px;background:#3b5fa0;flex:none}
.post-avatar{width:54px;height:54px;border-radius:50%;background:linear-gradient(135deg,#c9b9a6,#8d7b69);flex:none}
.post h4{color:var(--accent);font-size:12px;font-weight:700;text-transform:uppercase}

/* footer */
.site-footer{height:280px;background:var(--footer);color:#bbb;padding-top:40px}
.footer-top{display:flex;gap:40px}
.footer-links{flex:1}
.footer-top h3{color:var(--white);font-size:16px;font-weight:700;text-transform:uppercase;margin-bottom:14px}
.link-cols{display:flex;gap:50px}
.link-cols ul{list-style:none;font-size:12px}
.link-cols li::before{content:"›";color:var(--accent);margin-right:8px}
.newsletter{width:300px}
.news-form{display:flex;margin-bottom:18px}
.news-form .input{flex:1;height:30px;background:var(--white);color:#999;font-size:11px;padding:6px 10px}
.news-form .go{width:40px;height:30px;background:var(--accent)}
.cards{display:flex;gap:6px}
.cards span{width:38px;height:24px;background:#d9d9d9;border-radius:3px}
.footer-note{margin-top:26px;border-top:1px solid #3a3c40;padding-top:14px;font-size:10px;color:#888;text-align:center}
</style>
</head>
<body>

<header class="site-header">
  <div class="wrap">
    <div class="brand">
      <span class="brand-mark"></span>
      <div>
        <div class="brand-name">Pinebrook Stays</div>
        <div class="brand-sub">at Alder Ridge Holiday Park</div>
      </div>
    </div>
    <div class="header-info">
      <div class="social"><span></span><span></span><span></span><span></span><span></span></div>
      <div class="contact-line">
        <svg width="16" height="16" viewBox="0 0 24 24"><path fill="#1ba3dd" d="M6.6 10.8a15 15 0 0 0 6.6 6.6l2.2-2.2c.3-.3.7-.4 1-.2 1.1.4 2.3.6 3.6.6.6 0 1 .4 1 1V20c0 .6-.4 1-1 1C10.6 21 3 13.4 3 4c0-.6.4-1 1-1h3.5c.6 0 1 .4 1 1 0 1.3.2 2.5.6 3.6.1.3 0 .7-.2 1z"/></svg>
        01632 960 418
      </div>
      <div class="contact-mail">
        <svg width="14" height="10" viewBox="0 0 14 10"><rect x=".5" y=".5" width="13" height="9" fill="none" stroke="#999"/><path d="M.5 .5 7 5.5 13.5 .5" fill="none" stroke="#999"/></svg>
        info@pinebrookstays.com
      </div>
    </div>
  </div>
</header>

<nav class="main-nav">
  <ul>
    <li class="active">Home</li><li>News</li><li>Reviews</li><li>Caravans &amp; Lodges</li><li>Payment Plans</li><li>Alder Ridge</li><li>Local Attractions</li><li>Contact Us</li>
  </ul>
</nav>

<section class="hero">
  <div class="hero-bg" role="img" aria-label="Green holiday park meadow under a blue summer sky"></div>
  <div class="hero-copy">
    <h1>PRIVATE HOLIDAY RENTALS</h1>
    <p>Quality Lodge &amp; Caravan hire at Alder Ridge Holiday Park. Book online today!</p>
  </div>
  <form class="search-box">
    <div class="search-fields">
      <div class="field"><label>Check - IN</label><div class="input">dd/mm/yyyy</div></div>
      <div class="field"><label>Check - OUT</label><div class="input">dd/mm/yyyy</div></div>
    </div>
    <span class="btn">Submit</span>
  </form>
  <div class="hero-circle" role="img" aria-label="Family enjoying a holiday outside their lodge"></div>
  <div class="hero-arrows">
    <span><svg width="10" height="12"><path d="M8 1 2 6l6 5" fill="none" stroke="#fff" stroke-width="2"/></svg></span>
    <span><svg width="10" height="12"><path d="M2 1l6 5-6 5" fill="none" stroke="#fff" stroke-width="2"/></svg></span>
  </div>
</section>

<section class="overview">
  <h2 class="section-title">Overview of Company</h2>
  <p>Lorem ipsum dolor sit amet, consectetur adipisicing elit, sed do eiusmod tempor incididunt ut labore et dolore magna aliqua. Ut enim ad minim veniam, quis nostrud exercitation ullamco laboris nisi ut aliquip ex ea commodo consequat. Duis aute irure dolor in reprehenderit in voluptate velit esse cillum dolore eu fugiat nulla pariatur. Excepteur sint occaecat cupidatat non proident, sunt in culpa qui officia.</p>
  <span class="btn">Learn More</span>
</section>

<section class="late-deals">
  <div class="late-bg" role="img" aria-label="Warm evening town skyline at dusk"></div>
  <h2 class="section-title">Late Deals</h2>
  <div class="deal-grid">
    <article class="deal-card">
      <div class="deal-photo" role="img" aria-label="Caravan living room interior"></div>
      <span class="book-badge">BOOK<br>HERE</span>
      <div class="deal-body"><h3>THE MEADOW</h3><p>FRIDAY 04 SEPTEMBER 2015 (3 NIGHTS)</p></div>
    </article>
    <article class="deal-card">
      <div class="deal-photo" role="img" aria-label="Caravan kitchen and lounge interior"></div>
      <span class="book-badge">BOOK<br>HERE</span>
      <div class="deal-body"><h3>THE MEADOW</h3><p>FRIDAY 04 SEPTEMBER 2015 (3 NIGHTS)</p></div>
    </article>
    <article class="deal-card">
      <div class="deal-photo" role="img" aria-label="Lodge open-plan interior"></div>
      <span class="book-badge">BOOK<br>HERE</span>
      <div class="deal-body"><h3>THE MEADOW</h3><p>FRIDAY 04 SEPTEMBER 2015 (3 NIGHTS)</p></div>
    </article>
  </div>
  <div class="dots"><span class="on"></span><span></span></div>
</section>

<section class="caravans">
  <h2 class="section-title">List of Caravans &amp; Lodges</h2>
  <div class="caravan-grid">
    <article class="caravan-card">
      <div class="caravan-photo" role="img" aria-label="Caravan lounge interior"></div>
      <div class="caravan-info"><h3>THE HEATHER</h3>
        <div class="specs"><span>Caravan type</span><span>Caravan</span><span>Grade</span><span>Deluxe Plus</span><span>Sleeps: 6</span><span>Bedrooms: 3</span></div>
        <span class="btn">Get Details</span></div>
    </article>
    <article class="caravan-card">
      <div class="caravan-photo" role="img" aria-label="Lodge dining area interior"></div>
      <div class="caravan-info"><h3>THE HEATHER</h3>
        <div class="specs"><span>Caravan type</span><span>Caravan</span><span>Grade</span><span>Deluxe Plus</span><span>Sleeps: 6</span><span>Bedrooms: 3</span></div>
        <span class="btn">Get Details</span></div>
    </article>
    <article class="caravan-card">
      <div class="caravan-photo" role="img" aria-label="Caravan bedroom interior"></div>
      <div class="caravan-info"><h3>THE HEATHER</h3>
        <div class="specs"><span>Caravan type</span><span>Caravan</span><span>Grade</span><span>Deluxe Plus</span><span>Sleeps: 6</span><span>Bedrooms: 3</span></div>
        <span class="btn">Get Details</span></div>
    </article>
    <article class="caravan-card">
      <div class="caravan-photo" role="img" aria-label="Lodge living room interior"></div>
      <div class="caravan-info"><h3>THE HEATHER</h3>
        <div class="specs"><span>Caravan type</span><span>Caravan</span><span>Grade</span><span>Deluxe Plus</span><span>Sleeps: 6</span><span>Bedrooms: 3</span></div>
        <span class="btn">Get Details</span></div>
    </article>
  </div>
</section>

<section class="feeds">
  <div class="wrap">
    <div class="feed-col">
      <h2>Latest Reviews</h2>
      <div class="review"><h4>Maren Holt</h4><div class="meta">Stayed in New Hampshire <span class="stars">★★★★★</span></div>
        <p>Very clean on arrival. Very quiet location with fantastic views over the lake. We all had an amazing time. <span class="more">read more</span></p></div>
      <div class="review"><h4>Clara Denby</h4><div class="meta">Stayed in New Hampshire <span class="stars">★★★★★</span></div>
        <p>Very clean on arrival. Very quiet location with fantastic views over the lake. We all had an amazing time. <span class="more">read more</span></p></div>
    </div>
    <div class="feed-col">
      <h2>Social Feed</h2>
      <div class="post"><span class="post-icon"></span><div><h4>Consectetur Adip</h4><p>Lorem ipsum dolor sit amet, elit sed do eiusmod tempor incididunt ut labore et dolore magna aliqua.</p></div></div>
      <div class="post"><span class="post-icon"></span><div><h4>Finibus Bonorum</h4><p>Lorem ipsum dolor sit amet, elit sed do eiusmod tempor incididunt ut labore et dolore magna aliqua.</p></div></div>
      <div class="post"><span class="post-icon"></span><div><h4>Consectetur Adip</h4><p>Lorem ipsum dolor sit amet, elit sed do eiusmod tempor incididunt ut labore et dolore magna aliqua.</p></div></div>
    </div>
    <div class="feed-col">
      <h2>Blog Feed</h2>
      <div class="post"><span class="post-avatar" role="img" aria-label="Author portrait"></span><div><h4>Tom Ashby</h4><p>Lorem ipsum dolor sit amet, elit sed do eiusmod tempor incididunt ut labore et dolore magna aliqua.</p></div></div>
      <div class="post"><span class="post-avatar" role="img" aria-label="Author portrait"></span><div><h4>Iris Weller</h4><p>Lorem ipsum dolor sit amet, elit sed do eiusmod tempor incididunt ut labore et dolore magna aliqua.</p></div></div>
    </div>
  </div>
</section>

<footer class="site-footer">
  <div class="wrap">
    <div class="footer-top">
      <div class="footer-links">
        <h3>Useful Links</h3>
        <div class="link-cols">
          <ul><li>About us</li><li>News</li><li>Caravans &amp; Lodges</li><li>2015 Holidays</li><li>2016 Holidays</li><li>Late Deals</li></ul>
          <ul><li>Alder Ridge</li><li>Local Attractions</li><li>Website Guest</li><li>Contact Us</li><li>Reviews</li><li>Video Childrens Social</li></ul>
          <ul><li>Frequently Asked Questions</li><li>Park Entertainment Passes</li><li>Privacy Policy</li><li>Booking Terms</li></ul>
        </div>
      </div>
      <div class="newsletter">
        <h3>Newsletter</h3>
        <div class="news-form"><span class="input">Enter Email</span><span class="go"></span></div>
        <h3>Pay Through</h3>
        <div class="cards"><span></span><span></span><span></span><span></span><span></span></div>
      </div>
    </div>
    <p class="footer-note">Pinebrook Stays is an independent holiday letting business registered in England and Wales. All lodges and caravans are privately owned and let on behalf of their owners at Alder Ridge Holiday Park. Pinebrook Stays is not affiliated with the park operator. Prices and availability may change without notice. © 2015 Pinebrook Stays. All rights reserved.</p>
  </div>
</footer>

</body>
</html>
```